Moravel Aesthetic Doctor

I require an elegant, luxurious looking business card for my aesthetic business. I am a doctor and that will set me aside from competitors. I am planning to provide home and spa based treatments to clients with high expectations. I have attached my logo.

```html
<!DOCTYPE html>
<html lang="en">
<head>
<meta charset="utf-8">
<title>Moravel Aesthetic Doctor – Business Card</title>
<link href="https://fonts.googleapis.com/css2?family=Work+Sans:wght@400;500&display=swap" rel="stylesheet">
<style>
  :root {
    --stage: #d9d4cc;
    --card-top: #f4f5f6;
    --card-bottom: #e6e9eb;
    --deep-blue: #0a5cb0;
    --mid-blue: #1b86c9;
    --aqua: #35a9d6;
    --pale-aqua: #8fd0ea;
    --name-blue: #1a86c0;
    --ink: #2b2f33;
    --rule: #2ba3c9;
    --brand-grey: #7b8489;
  }
  html, body {
    margin: 0;
    width: 1200px;
    height: 887px;
    overflow: hidden;
    background: var(--stage);
    font-family: "Work Sans", sans-serif;
  }
  .card {
    position: absolute;
    left: 80px;
    top: 157px;
    width: 1040px;
    height: 574px;
    border-radius: 24px;
    background: linear-gradient(160deg, var(--card-top), var(--card-bottom));
    box-shadow: 0 10px 30px rgba(0,0,0,0.15);
    overflow: hidden;
  }
  .card__band {
    position: absolute;
    left: 0;
    top: 0;
    width: 100%;
    height: 170px;
    background:
      linear-gradient(to bottom, rgba(244,245,246,0) 55%, var(--card-top) 100%),
      linear-gradient(to right, var(--pale-aqua) 0%, var(--aqua) 30%, var(--mid-blue) 60%, var(--deep-blue) 100%);
  }
  .brand {
    position: absolute;
    left: 54px;
    top: 160px;
    display: flex;
    align-items: center;
    gap: 20px;
  }
  .brand__dot {
    width: 96px;
    height: 96px;
    border-radius: 50%;
    border: 2px solid #9aa3a8;
    box-sizing: border-box;
  }
  .brand__name {
    font-size: 36px;
    font-weight: 400;
    letter-spacing: 3px;
    color: var(--brand-grey);
    line-height: 1.1;
    text-transform: uppercase;
  }
  .brand__name span { display: block; font-size: 22px; letter-spacing: 2px; }
  .holder {
    position: absolute;
    right: 52px;
    top: 276px;
    text-align: right;
  }
  .holder__name {
    margin: 0;
    font-size: 27px;
    font-weight: 500;
    color: var(--name-blue);
  }
  .holder__title {
    margin: 6px 0 0;
    font-size: 21px;
    line-height: 31px;
    color: var(--ink);
    letter-spacing: 0.5px;
  }
  .card__rule {
    position: absolute;
    left: 45px;
    right: 52px;
    top: 400px;
    border-top: 1.5px solid var(--rule);
  }
  .contacts {
    position: absolute;
    left: 45px;
    top: 436px;
    margin: 0;
    padding: 0;
    list-style: none;
    font-size: 22px;
    color: var(--ink);
    letter-spacing: 1px;
  }
  .contacts li {
    display: flex;
    align-items: center;
    gap: 10px;
    height: 33px;
  }
  .contacts svg { width: 15px; height: 15px; flex: none; }
</style>
</head>
<body>
  <div class="card">
    <div class="card__band" role="img" aria-label="Decorative flowing blue wave band across the top of the card"></div>

    <div class="brand">
      <div class="brand__dot"></div>
      <div class="brand__name">Moravel<span>Aesthetic Doctor</span></div>
    </div>

    <div class="holder">
      <h1 class="holder__name">Dr Elise Varden MRCPCH MD</h1>
      <p class="holder__title">Australasian Diploma<br>of Aesthetic Medicine</p>
    </div>

    <div class="card__rule"></div>

    <ul class="contacts">
      <li>
        <svg viewBox="0 0 16 16"><path d="M3 1.5 L6 1 L7.5 4.5 L5.5 6 C6.5 8 8 9.5 10 10.5 L11.5 8.5 L15 10 L14.5 13 C14 14.5 12 15 10 14 C6 12 3 9 1.5 5 C1 3.5 1.5 2 3 1.5 Z" fill="var(--name-blue)"/></svg>
        0800 555 014
      </li>
      <li>
        <svg viewBox="0 0 16 16"><rect x="1.5" y="3.5" width="13" height="9" rx="1" fill="none" stroke="var(--name-blue)" stroke-width="1.6"/><path d="M2 4 L8 9 L14 4" fill="none" stroke="var(--name-blue)" stroke-width="1.6"/></svg>
        elise@moravel.co.nz
      </li>
      <li>
        <svg viewBox="0 0 16 16"><circle cx="8" cy="8" r="6.5" fill="none" stroke="var(--name-blue)" stroke-width="1.4"/><ellipse cx="8" cy="8" rx="3" ry="6.5" fill="none" stroke="var(--name-blue)" stroke-width="1.2"/><path d="M1.5 8 H14.5" stroke="var(--name-blue)" stroke-width="1.2"/></svg>
        www.moravel.co.nz
      </li>
    </ul>
  </div>
</body>
</html>
```